Webpages for Vuolahtinen Software Consulting

Needed: Webpage design.
Details:
One page site with good looking fonts and simple modern design. Logo would also be nice.
Page is for Software consulting company called: "Vuolahtinen Software Consulting". Vuolahtinen is my surname.
Pages should tell viewer that the company is reliable and its employees are hard-core professionals.
Company currently has one employee, that's me. So what I do is what this company does. I am software consultant. Basicly that means that I do Java/JavaEE/Web programming as subcontractor.
Here is more detail information about me.
SPECIALTIES
- Enterprise J2EE Application Programming and Architectures,
- Web development and
- Agile development.
I have over a decade of experience on designing and creating Java based web-services and applications to multiple interfaces. I also have plenty of experience about software architectures, design patterns and integration into third party systems. I’ve got good knowledge about agile software development and testing processes and I am experienced ScrumMaster and software project leader.
Target Market(s)
IT Businesses, Coding companies... Anyone who is buying coding as service.
Industry/Entity Type
Software
Look and feel

```html
<!DOCTYPE html>
<html lang="en">
<head>
<meta charset="utf-8">
<title>Vuolahtinen Software Consulting</title>
<link rel="stylesheet" href="https://fonts.googleapis.com/css2?family=Cabin:wght@400;500&family=Carlito&family=Arimo:wght@400;700&display=swap">
<style>
:root{
  --red:#b30f0f;
  --ink:#1e1e1e;
  --text:#222;
  --nav-top:#4a4d52;
  --nav-bottom:#1a1b1e;
  --panel:#f4f4f4;
  --line:#b9b9b9;
  --white:#fff;
}
*{box-sizing:border-box;margin:0;padding:0}
html,body{width:851px;height:1200px;overflow:hidden;background:var(--white)}
body{position:relative;font-family:"Carlito",sans-serif;color:var(--text)}
.abs{position:absolute}
.header-band{left:0;top:0;width:851px;height:70px;background:linear-gradient(#fff,#f1f1f1)}
.brand{left:38px;top:12px;font-family:"Cabin",sans-serif;font-size:30px;color:var(--red);font-weight:400}
.search{left:696px;top:22px;width:127px;height:28px;border:1px solid #9a9a9a;border-radius:5px;background:linear-gradient(#fff,#ececec);font:13px "Arimo",sans-serif;padding:6px 15px;color:#222}
.search-btn{position:absolute;right:4px;top:4px;width:19px;height:19px;border-radius:50%;background:var(--red);border:1px solid #700}
.search-btn svg{position:absolute;left:4px;top:4px}
.nav{left:15px;top:70px;width:822px;height:37px;background:linear-gradient(var(--nav-top),var(--nav-bottom));border-radius:3px;font:12.5px "Arimo",sans-serif;color:var(--white)}
.nav span{position:absolute;top:10px}
.nav .active{left:20px;top:0;width:78px;height:37px;background:#000;padding:10px 0 0 20px}
.hero{left:15px;top:113px;width:822px;height:250px;border-radius:3px;background:linear-gradient(#f4f6f8 0%,#e8eef3 60%,#c5d9e6 100%);box-shadow:0 8px 10px -6px rgba(0,0,0,.35)}
.hero-photo{position:absolute;left:0;top:0;width:330px;height:250px;background:linear-gradient(90deg,#cfd2d4 0%,#e6e7e7 60%,rgba(232,238,243,0) 100%)}
.hero h2{position:absolute;left:403px;top:24px;font:400 21px "Cabin",sans-serif;color:var(--ink)}
.hero ul{position:absolute;left:410px;top:70px;list-style:none;font:400 16px "Cabin",sans-serif;color:var(--ink);line-height:20px}
.hero li{position:relative;padding-left:22px;margin-bottom:19px;width:360px}
.hero li svg{position:absolute;left:0;top:5px}
.dots{left:393px;top:382px;display:flex;gap:2px}
.dots i{width:17px;height:17px;border-radius:50%;background:#2b2c30}
.dots i:first-child{background:#8d0b0b}
.intro{left:0;top:405px;width:851px;height:226px;background:var(--panel)}
.intro h1,.intro h3{position:absolute;font:400 22px "Cabin",sans-serif;color:var(--ink)}
.intro h1 em,.intro h3 em,.service-label em{font-style:normal;color:var(--red)}
.intro p{position:absolute;font-size:11px;line-height:15.2px;color:#111}
.more-btn{position:absolute;width:76px;height:27px;border:1px solid #9c9c9c;border-radius:5px;background:linear-gradient(#fff,#e9e9e9);font:10px "Arimo",sans-serif;color:var(--red);text-align:center;line-height:25px}
.services{left:0;top:631px;width:851px;height:249px;background:linear-gradient(#dcdcdc 0%,#f4f4f4 35%,#fff 100%)}
.cloud{position:absolute;top:22px;width:208px;height:168px}
.service-label{position:absolute;top:197px;width:240px;text-align:center;font:400 19px "Cabin",sans-serif;color:var(--ink)}
.arrow{position:absolute;top:82px;width:24px;height:24px;border-radius:50%;background:linear-gradient(#fff,#e2e2e2);border:1px solid #ccc}
.arrow svg{position:absolute;left:8px;top:7px}
.lower{left:0;top:880px;width:851px;height:246px;background:linear-gradient(#e6e6e6 0%,#fff 40px)}
.col-head{position:absolute;top:32px;width:210px;height:34px;background:linear-gradient(90deg,#fff 0%,#ededed 60%,#e0e0e0 100%);border-bottom:1px solid #aaa;font:400 15px "Arimo",sans-serif;color:#333;padding:9px 0 0 25px}
.avatar{position:absolute;left:36px;width:55px;height:52px;background:linear-gradient(#8e9a6a,#5d5130)}
.post{position:absolute;left:100px;font:9.5px/13.5px "Arimo",sans-serif;color:#222;width:170px;white-space:nowrap}
.post b{display:block;font-weight:400;color:var(--red);margin-bottom:3px}
.news{position:absolute;left:366px;font:9.5px/13.5px "Arimo",sans-serif;color:#222;width:170px;white-space:nowrap}
.cal{position:absolute;left:328px}
.link{position:absolute;font:10px "Arimo",sans-serif;color:var(--red)}
.field{left:617px;top:968px;width:169px;height:26px;border:1px solid #888;background:#fff}
.subscribe{left:626px;top:1012px;width:124px;height:27px;border-radius:3px;background:linear-gradient(#3a3a3a,#000);color:#fff;font:11px "Arimo",sans-serif;text-align:center;line-height:27px}
.footer{left:15px;top:1126px;width:822px;height:63px;border-radius:3px;background:linear-gradient(var(--nav-top),var(--nav-bottom));color:#ddd;font:10.5px "Arimo",sans-serif}
.social{position:absolute;top:19px;width:24px;height:24px;border-radius:4px}
.footer-links{position:absolute;left:367px;top:12px;white-space:nowrap}
.footer-links span{margin:0 12px}
.copyright{position:absolute;left:395px;top:38px;white-space:nowrap}
</style>
</head>
<body>
<div class="abs header-band"></div>
<div class="abs brand">Vuolahtinen</div>
<div class="abs search">Search<span class="search-btn"><svg width="10" height="10" viewBox="0 0 10 10"><path d="M1 2l3 3-3 3M5 2l3 3-3 3" stroke="#fff" stroke-width="1.5" fill="none"/></svg></span></div>

<nav class="abs nav">
  <span class="active">HOME</span>
  <span style="left:128px">ABOUT US</span><span style="left:216px">|</span>
  <span style="left:245px">PROJECTS</span><span style="left:336px">|</span>
  <span style="left:365px">SERVICES</span><span style="left:452px">|</span>
  <span style="left:481px">LOGIN</span><span style="left:549px">|</span>
  <span style="left:578px">CONTACT US</span>
</nav>

<section class="abs hero">
  <div class="hero-photo" role="img" aria-label="Photo of two consultants in business suits at a laptop"></div>
  <h2>Software Consulting</h2>
  <ul>
    <li><svg width="9" height="11" viewBox="0 0 9 11"><path d="M1 1l6 4.5-6 4.5" stroke="#444" stroke-width="2.4" fill="none"/></svg>Enterprise Server Application Programming and Architectures</li>
    <li><svg width="9" height="11" viewBox="0 0 9 11"><path d="M1 1l6 4.5-6 4.5" stroke="#444" stroke-width="2.4" fill="none"/></svg>Web development</li>
    <li><svg width="9" height="11" viewBox="0 0 9 11"><path d="M1 1l6 4.5-6 4.5" stroke="#444" stroke-width="2.4" fill="none"/></svg>Agile development.</li>
  </ul>
</section>
<div class="abs dots"><i></i><i></i><i></i><i></i></div>

<section class="abs intro">
  <h1 style="left:30px;top:16px">Welcome to <em>Vuolahtinen</em></h1>
  <p style="left:31px;top:55px;width:436px">Lorem ipsum dolor sit amet, consectetuer adipiscing elit. Nam nibh. Nunc varius facilisis eros.<br>Sed erat. In in velit quis arcu ornare laoreet. Curabitur adipiscing luctus massa. Integer ut<br>purus ac augue commodo commodo. Nunc nec mi eu justo tempor consectetuer. Etiam<br>vitae nisl.</p>
  <p style="left:31px;top:132px;width:436px">Lorem ipsum dolor sit amet, consectetuer adipiscing elit. Nam nibh. Nunc varius facilisis eros.<br>Sed erat. In in velit quis arcu ornare laoreet. Curabitur adipiscing luctus massa. Integer ut<br>purus ac augue commodo commodo. Nunc nec mi eu justo tempor consectetuer.</p>
  <a class="more-btn" style="left:332px;top:187px">View more</a>
  <h3 style="left:556px;top:17px">What we <em>Do?</em></h3>
  <p style="left:547px;top:51px;width:290px">Lorem ipsum dolor sit amet, consectetuer adipiscing elit.<br>Nam nibh. Nunc varius facilisis eros. Sed erat. In in velit quis<br>arcu ornare laoreet. Curabitur adipiscing luctus massa.</p>
  <p style="left:547px;top:112px;width:290px">Integer ut purus ac augue commodo commodo. Nunc nec mi<br>eu justo tempor consectetuer. Etiam vitae nisl.</p>
  <p style="left:547px;top:158px;width:290px">Lorem ipsum dolor sit amet, consectetuer adipiscing elit.</p>
  <a class="more-btn" style="left:733px;top:187px">View more</a>
</section>

<section class="abs services">
  <span class="arrow" style="left:16px"><svg width="7" height="9" viewBox="0 0 7 9"><path d="M5 1L2 4.5 5 8" stroke="#222" stroke-width="2" fill="none"/></svg></span>
  <div class="cloud" style="left:53px" role="img" aria-label="Illustration of a globe in a cloud frame, web development"><svg width="208" height="168"><ellipse cx="104" cy="84" rx="100" ry="78" fill="#fff" stroke="#1a1a1a" stroke-width="4"/><circle cx="104" cy="84" r="38" fill="#5aa0d6"/></svg></div>
  <div class="service-label" style="left:40px">Web <em>Development</em></div>
  <div class="cloud" style="left:309px" role="img" aria-label="Illustration of a paintbrush and colour drops in a cloud frame, web design"><svg width="208" height="168"><ellipse cx="104" cy="84" rx="100" ry="78" fill="#fff" stroke="#1a1a1a" stroke-width="4"/><ellipse cx="104" cy="100" rx="55" ry="20" fill="#d9c9a0"/></svg></div>
  <div class="service-label" style="left:296px">Web <em>Design</em></div>
  <div class="cloud" style="left:573px" role="img" aria-label="Illustration of blue 3D lettering with tools in a cloud frame, web services"><svg width="208" height="168"><ellipse cx="104" cy="84" rx="100" ry="78" fill="#fff" stroke="#1a1a1a" stroke-width="4"/><rect x="44" y="50" width="120" height="56" rx="8" fill="#3a6fc4"/></svg></div>
  <div class="service-label" style="left:583px">Web <em>Services</em></div>
  <span class="arrow" style="left:798px"><svg width="7" height="9" viewBox="0 0 7 9"><path d="M2 1l3 3.5L2 8" stroke="#222" stroke-width="2" fill="none"/></svg></span>
</section>

<section class="abs lower">
  <div class="col-head" style="left:30px">Blog</div>
  <div class="col-head" style="left:320px">Latest News</div>
  <div class="col-head" style="left:593px;padding-top:13px">Newsletter</div>
</section>

<div class="avatar" style="top:954px" role="img" aria-label="Author portrait"></div>
<div class="post" style="top:951px"><b>Dec 1, 2011</b>Lorem Ipsum is simply dummy text<br>Lorem Ipsum is simplyLorem Ipsum<br>is simply dummy&nbsp; text.</div>
<div class="avatar" style="top:1020px" role="img" aria-label="Author portrait"></div>
<div class="post" style="top:1019px"><b>Dec 1, 2011</b>Lorem Ipsum is simply dummy text<br>Lorem Ipsum is simplyLorem Ipsum<br>is simply dummy&nbsp; text.</div>
<span class="link" style="left:103px;top:1080px">View more</span>

<svg class="cal" style="top:958px" width="30" height="40" viewBox="0 0 30 40"><rect x="2" y="4" width="26" height="33" rx="3" fill="#f3f3f3" stroke="#555" stroke-width="1.5"/><rect x="2" y="4" width="26" height="9" rx="3" fill="#c62020"/><text x="15" y="31" text-anchor="middle" font-family="Arimo,sans-serif" font-size="13" font-weight="700" fill="#222">15</text></svg>
<div class="news" style="top:961px">Lorem Ipsum is simply dummy text<br>Lorem Ipsum is simplyLorem Ipsum<br>is simply dummy&nbsp; text.</div>
<svg class="cal" style="top:1022px" width="30" height="40" viewBox="0 0 30 40"><rect x="2" y="4" width="26" height="33" rx="3" fill="#f3f3f3" stroke="#555" stroke-width="1.5"/><rect x="2" y="4" width="26" height="9" rx="3" fill="#c62020"/><text x="15" y="31" text-anchor="middle" font-family="Arimo,sans-serif" font-size="13" font-weight="700" fill="#222">15</text></svg>
<div class="news" style="top:1021px">Lorem Ipsum is simply dummy text<br>Lorem Ipsum is simplyLorem Ipsum<br>is simply dummy&nbsp; text.</div>
<span class="link" style="left:371px;top:1077px">View more</span>

<div class="abs field"></div>
<div class="abs subscribe">Subscribe</div>

<footer class="abs footer">
  <span class="social" style="left:33px;background:#2d55a0"></span>
  <span class="social" style="left:69px;background:#3fa7dc"></span>
  <span class="social" style="left:107px;background:#e8702a"></span>
  <div class="footer-links">Privacy Policy<span>|</span>Terms &amp; Conditions<span>|</span>Contact Us</div>
  <div class="copyright">Copyright © Vuolahtinen, All Rights Reserved</div>
</footer>
</body>
</html>
```